****Business Card Design for Quarrystone Development. Design based around attached logo/company name

I’m looking for business card design for my company Quarrystone Development Group,LLC. Design should be professional, sharp and minimal. Outside of the attached logos, greyscale colors for remainder of cards. My thoughts are two-sided card with attached logo on one side and my info on the other but open to one-sided as well with right design.
Target Market(s)
Real estate professionals including banks, private investors, property owners, developers, commercial tenants like Brewlantern, Grovika or Tanquist’s.
Industry/Entity Type
Commercial real estate development and investments.
Contact Information for Business Card
Name, title, email, phone #’s, web address and physical address
Font styles to use
Other font styles liked:
- Helvetica, Garamond, etc
Colors
Designer to choose only greyscale colors for use in the design.
Requirements
Must have
- Attached logo first or second options.
Nice to have
- Two sided card with logo on one side. Attached Logo/company name can be laid out any way that flows as long as it’s legible.name
Should not have
- No loud colors. ***Please do not include logo, I have removed the company design with a logo image.

```html
<!DOCTYPE html>
<html lang="en">
<head>
<meta charset="utf-8">
<title>Quarrystone Development Group,LLC — Business Card</title>
<link href="https://fonts.googleapis.com/css2?family=EB+Garamond:wght@500;700&family=Arimo:wght@400&display=swap" rel="stylesheet">
<style>
  :root {
    --page: #e6e2dc;
    --card-top: #f4f2ee;
    --card-bottom: #e9e5df;
    --ink-dark: #3a4150;
    --ink-mid: #5c5f66;
    --accent-line: #b9a58c;
    --card-edge: #d4cfc7;
  }
  * { margin: 0; padding: 0; box-sizing: border-box; }
  html, body {
    width: 1200px; height: 897px; overflow: hidden;
    background: var(--page);
  }
  .canvas { position: relative; width: 1200px; height: 897px; }
  .card {
    position: absolute; left: 100px; top: 176px;
    width: 1000px; height: 545px;
    border-radius: 22px; overflow: hidden;
    background: linear-gradient(160deg, var(--card-top), var(--card-bottom));
    border: 1px solid var(--card-edge);
    box-shadow: 0 12px 30px rgba(0,0,0,0.12);
  }
  .card-band { position: absolute; left: 0; top: 0; width: 1000px; height: 545px; }
  .company-name {
    position: absolute; left: 100px; top: 236px; width: 380px;
    font-family: "EB Garamond", Garamond, serif; font-weight: 500;
    font-size: 30px; line-height: 1.15; letter-spacing: 1.5px;
    color: var(--ink-dark); text-transform: uppercase; text-align: center;
  }
  .contact { position: absolute; left: 550px; top: 150px; }
  .person-name {
    font-family: "EB Garamond", Garamond, serif; font-weight: 700;
    font-size: 28px; letter-spacing: 0.5px; color: var(--ink-dark);
    text-transform: uppercase; line-height: 1.1;
  }
  .person-title, .address, .contact-line {
    font-family: Arimo, Helvetica, Arial, sans-serif; font-weight: 400;
    color: var(--ink-mid);
  }
  .person-title { font-size: 21px; line-height: 1.2; }
  .address { margin-top: 26px; font-size: 21px; line-height: 27px; }
  .contact-list { list-style: none; margin-top: 26px; }
  .contact-line {
    display: flex; align-items: center; gap: 10px;
    font-size: 20px; line-height: 33px;
  }
  .contact-icon { width: 18px; height: 18px; flex: none; }
</style>
</head>
<body>
<main class="canvas">
  <section class="card" aria-label="Business card">
    <svg class="card-band" viewBox="0 0 1000 545" aria-hidden="true">
      <defs>
        <linearGradient id="bandShade" x1="0" y1="0" x2="1" y2="0">
          <stop offset="0" stop-color="#4a4a50"/>
          <stop offset="0.5" stop-color="#3b3c42"/>
          <stop offset="1" stop-color="#2a2b30"/>
        </linearGradient>
      </defs>
      <path d="M0,438 C260,530 660,540 1000,408 L1000,545 L0,545 Z" fill="url(#bandShade)"/>
      <path d="M0,424 C250,500 650,520 930,470" fill="none" stroke="var(--accent-line)" stroke-width="3"/>
    </svg>

    <div class="company-name">Quarrystone Development Group,LLC</div>

    <div class="contact">
      <h1 class="person-name">Dorian Vasek</h1>
      <p class="person-title">Founder/CEO</p>
      <p class="address">2190 Harbor Point Road<br>Lakeside MN 5620</p>
      <ul class="contact-list">
        <li class="contact-line">
          <svg class="contact-icon" viewBox="0 0 24 24" aria-hidden="true"><path fill="#3a4150" d="M6.6 10.8a15.1 15.1 0 0 0 6.6 6.6l2.2-2.2c.3-.3.7-.4 1-.2 1.1.4 2.3.6 3.6.6.6 0 1 .4 1 1V20c0 .6-.4 1-1 1A17 17 0 0 1 3 4c0-.6.4-1 1-1h3.5c.6 0 1 .4 1 1 0 1.3.2 2.5.6 3.6.1.3 0 .7-.2 1z"/></svg>
          (123)-555-0148
        </li>
        <li class="contact-line">
          <svg class="contact-icon" viewBox="0 0 24 24" aria-hidden="true"><path fill="#3a4150" d="M2 5h20v3l-10 6L2 8zm0 5 10 6 10-6v9H2z"/></svg>
          info@quarrystonedevelopment.com
        </li>
        <li class="contact-line">
          <svg class="contact-icon" viewBox="0 0 24 24" aria-hidden="true"><circle cx="12" cy="12" r="9" fill="none" stroke="#3a4150" stroke-width="2"/><path d="M3 12h18M12 3c3 3 3 15 0 18M12 3c-3 3-3 15 0 18" fill="none" stroke="#3a4150" stroke-width="1.6"/></svg>
          www.quarrystonedevelopment.com
        </li>
      </ul>
    </div>
  </section>
</main>
</body>
</html>
```